Young, dynamic furniture company needs a new business card design

We require a new business card design for our modern furniture company which supplies furniture and appliances to the property and development market.
Oakridge Interiors has become one of the leading furniture & appliance suppliers to the property market withing London. With over 10 years experience, we have increased our business to supply not only private landlords and managing agents, but also property developers, housing associations and local councils.
We offer not only a complete range of furniture which includes beds, wardrobes, dining sets and sofas, but also a high quality, full delivery and assembly service to help you with all our furnishing needs.

Target Market(s)

Private landlords, estate agents, letting agents, property management companies

Industry/Entity Type

Business

Contact Information for Business Card

Name,
Title,
Address,
Mobile,
Telephone,
Fax, Website, email address

Font styles to use
Sans Serif

Colors
3176b5
0555a3
85abd2
cfdeed

Requirements
Must have
• All the above information for each of our staff, along with our logo

```html
<!DOCTYPE html>
<html lang="en">
<head>
<meta charset="utf-8">
<title>Oakridge Interiors – Business Card</title>
<link rel="stylesheet" href="https://fonts.googleapis.com/css2?family=Open+Sans:wght@400;600&display=swap">
<style>
  :root {
    --page: #e9ebee;
    --card-white: #f2f2f2;
    --sky: #85abd2;
    --royal: #0555a3;
    --mid-blue: #3176b5;
    --navy: #25264a;
    --charcoal: #333333;
    --line: #ffffff;
  }
  html, body {
    margin: 0;
    width: 1200px;
    height: 900px;
    overflow: hidden;
    background: var(--page);
    font-family: "Open Sans", Arial, sans-serif;
  }
  .stage {
    position: relative;
    width: 1200px;
    height: 900px;
  }
  .card {
    position: absolute;
    left: 320px;
    width: 560px;
    height: 320px;
    background: var(--card-white);
    overflow: hidden;
    box-shadow: 0 6px 18px rgba(0,0,0,0.18);
  }
  .card--front { top: 100px; }
  .card--back { top: 480px; }
  .card__art {
    position: absolute;
    inset: 0;
    width: 560px;
    height: 320px;
  }
  .brand {
    position: absolute;
    display: flex;
    align-items: center;
    gap: 8px;
    color: var(--navy);
  }
  .brand__mark {
    width: 14px;
    height: 14px;
    background: var(--navy);
  }
  .brand__name {
    font-weight: 600;
    font-size: 17px;
    letter-spacing: 0.5px;
    text-transform: uppercase;
    line-height: 1;
  }
  .brand__tagline {
    font-size: 7px;
    letter-spacing: 1px;
    text-transform: uppercase;
    margin-top: 3px;
  }
  .card--front .brand { left: 160px; top: 72px; }
  .card--back .brand { left: 26px; top: 90px; }
  .person {
    position: absolute;
    right: 42px;
    top: 92px;
    text-align: center;
    color: var(--mid-blue);
  }
  .person__name { font-size: 30px; line-height: 1; }
  .person__title { font-size: 14px; color: var(--line); }
  .contact {
    position: absolute;
    left: 86px;
    top: 170px;
    margin: 0;
    padding: 0;
    list-style: none;
    color: var(--royal);
    font-size: 15px;
    line-height: 18px;
  }
  .contact li + li { margin-top: 0; }
  .contact .gap { margin-top: 12px; }
</style>
</head>
<body>
<main class="stage">

  <section class="card card--front" aria-label="Business card front">
    <svg class="card__art" viewBox="0 0 560 320" aria-hidden="true">
      <polygon points="0,210 560,40 560,320 0,320" fill="var(--sky)"/>
      <line x1="150" y1="312" x2="560" y2="178" stroke="var(--line)" stroke-width="2"/>
      <polygon points="170,320 560,192 560,320" fill="var(--royal)"/>
    </svg>
    <div class="brand">
      <span class="brand__mark"></span>
      <div>
        <div class="brand__name">Oakridge Interiors</div>
        <div class="brand__tagline">Home furnishing solutions</div>
      </div>
    </div>
  </section>

  <section class="card card--back" aria-label="Business card back">
    <svg class="card__art" viewBox="0 0 560 320" aria-hidden="true">
      <polygon points="0,190 560,30 560,320 0,320" fill="var(--sky)"/>
      <line x1="120" y1="318" x2="560" y2="176" stroke="var(--line)" stroke-width="2"/>
      <polygon points="140,320 560,188 560,320" fill="var(--royal)"/>
      <polygon points="0,190 72,170 72,320 0,320" fill="var(--charcoal)"/>
      <g class="icons" fill="var(--line)" stroke="var(--line)">
        <!-- phone -->
        <path d="M30 196 q-3 0 -3 4 q2 8 10 11 q4 0 4 -3 l-3 -3 l-3 2 q-3 -2 -4 -5 l2 -2 z" stroke="none"/>
        <!-- envelope -->
        <rect x="27" y="226" width="16" height="11" fill="none" stroke-width="1.5"/>
        <polyline points="27,226 35,233 43,226" fill="none" stroke-width="1.5"/>
        <!-- globe -->
        <circle cx="35" cy="260" r="8" fill="none" stroke-width="1.5"/>
        <line x1="27" y1="260" x2="43" y2="260" stroke-width="1.2"/>
        <ellipse cx="35" cy="260" rx="3.5" ry="8" fill="none" stroke-width="1.2"/>
        <!-- pin -->
        <path d="M35 298 l-6 -9 a7 7 0 1 1 12 0 z" stroke="none"/>
        <circle cx="35" cy="285" r="2.5" fill="var(--charcoal)" stroke="none"/>
      </g>
    </svg>
    <div class="brand">
      <span class="brand__mark"></span>
      <div>
        <div class="brand__name">Oakridge Interiors</div>
        <div class="brand__tagline">Home furnishing solutions</div>
      </div>
    </div>
    <div class="person">
      <div class="person__name">Name</div>
      <div class="person__title">Title</div>
    </div>
    <ul class="contact">
      <li>0207-418-552</li>
      <li>0798-203-617</li>
      <li class="gap">email@email.com</li>
      <li class="gap">company.com</li>
      <li class="gap">Address</li>
    </ul>
  </section>

</main>
</body>
</html>
```